Sleep/Snoring Business - Requires Website - Australia

We are seeking a simple to maintain website for our sleep business. The health care business provides diagnostic and treatment solutions for snoring, sleep disorders and other respiratory problems.

Ideally, colours to match the company logo (attached).

The page must be built using WORDPRESS.

Ideally site will have a home page outlining the business, with 5 sub pages - being "Diagnosis" "Treatment Options", "Prodcuts", "About Us", "Contact Us"

The site home page should include a large picture on the home page.

The "Treatment Options" and "Diagnosis" pages must include:
Allow for a few pictures with assocaited text, plus space for some embeded youtube videos.

"Prodcuts" page should have the ability to show 3-4 products across the page with text below.. that can include external URL to products

The "About Us" page must include:
1. a Map (google map) to identify the various locations. There are 6 in total.
2. A Section to describe our doctors/staff - allow for a picture and some text

The "Contact Us" page must include:
email form
telephone details

The overall design should have a clean and medical/safe feeling

Target Market(s)

People who snore and those with sleeping and respiratory disorders

Industry/Entity Type

Health Care

Coding

Coded - Design and coding required

Number of Pages Required

5+ page

Colors

Designer to choose colors to be used in the design.

Requirements
Must have
• The page must be built using WORDPRESS.
• Ideally site will have a home page outlining the business, with 5 sub pages - being "Diagnosis" "Treatment Options", "Prodcuts", "About Us", "Contact Us"
• The site home page should include a large picture on the home page.
• The "Treatment Options" and "Diagnosis" pages must include:
• Allow for a few pictures with assocaited text, plus space for some embeded youtube videos.
• "Prodcuts" page should have the ability to show 3-4 products across the page with text below.. that can include external URL to products
• The "About Us" page must include:
• 1. a Map (google map) to identify the various locations. There are 6 in total.
• 2. A Section to describe our doctors/staff - allow for a picture and some text
• The "Contact Us" page must include:
• email form
• telephone details
• Pictures must be licenced or free to use
Nice to have
• Home page pictures showing people sleeping well, snoring or fresh air (landscape) type transition pictures (at least 3).
Should not have
• Not to look cheap
• This is a high end healthcare business, so must look that way

```html
<!DOCTYPE html>
<html lang="en">
<head>
<meta charset="utf-8">
<title>Restwell – Diagnostic &amp; Treatment Solution</title>
<link href="https://fonts.googleapis.com/css2?family=Open+Sans:ital,wght@0,400;0,600;0,700;1,400;1,600&family=Oswald:wght@300;700&family=Raleway:wght@500;600;700&display=swap" rel="stylesheet">
<style>
:root{
  --navy:#0b4a85;
  --navy-deep:#083d70;
  --sky:#a9b8dc;
  --ink:#2b2b2b;
  --muted:#6b6b6b;
  --line:#e3e3e3;
  --panel:#f7f7f7;
  --footer:#2b2a30;
  --footer-base:#201f24;
  --white:#ffffff;
}
*{margin:0;padding:0;box-sizing:border-box}
html,body{width:1200px;height:2308px;overflow:hidden;background:var(--white)}
body{position:relative;font-family:"Open Sans",sans-serif;color:var(--ink)}
.abs{position:absolute}
.btn{position:absolute;display:flex;align-items:center;justify-content:center;font-family:"Raleway",sans-serif;font-weight:700;text-transform:uppercase;border:1.5px solid var(--navy);color:var(--navy);background:var(--white);font-size:12px;letter-spacing:.2px}

/* header */
.site-header{position:absolute;left:0;top:0;width:1200px;height:112px;background:var(--white);border-bottom:4px solid var(--sky);z-index:3}
.brand{position:absolute;left:131px;top:28px;display:flex;align-items:center;gap:10px;font-family:"Raleway",sans-serif;font-weight:700;font-size:44px;color:var(--navy);letter-spacing:-1px}
.brand-dot{width:14px;height:14px;border-radius:50%;background:var(--navy)}
.phone{position:absolute;left:705px;top:17px;display:flex;align-items:center;gap:9px;font-size:10.5px;color:var(--muted);white-space:nowrap}
.phone-icon{width:32px;height:32px;border-radius:50%;background:var(--sky);display:flex;align-items:center;justify-content:center}
.phone strong{font-size:13.5px;color:var(--ink);font-weight:700}
.appt{position:absolute;left:909px;top:18px;width:158px;height:32px;background:var(--navy);color:var(--white);font-family:"Raleway",sans-serif;font-weight:700;font-size:12px;display:flex;align-items:center;justify-content:center}
.main-nav{position:absolute;top:80px;left:0;width:1200px;font-family:"Raleway",sans-serif;font-weight:600;font-size:12.5px;color:var(--ink)}
.main-nav span{position:absolute;white-space:nowrap}
.main-nav .current{color:var(--navy)}
.nav-mark{position:absolute;left:452px;top:108px;width:52px;height:4px;background:var(--navy)}

/* hero */
.hero-photo{position:absolute;left:0;top:112px;width:1200px;height:560px;background:linear-gradient(100deg,#f3f3f3 0%,#eceff3 35%,#c9d6e4 60%,#dbe7ee 80%,#f1f1f1 100%)}
.hero-curve{position:absolute;left:0;top:440px;width:1200px;height:425px}
.hero-kicker{left:131px;top:220px;font-family:"Oswald",sans-serif;font-weight:300;font-size:30px;color:#333}
.hero-title{left:131px;top:260px;font-family:"Oswald",sans-serif;font-weight:700;font-size:40px;color:#2a2a2a;letter-spacing:.5px}
.hero-text{left:131px;top:322px;width:360px;font-size:14.5px;line-height:24px;color:#444}
.slide-arrow{position:absolute;top:296px;width:44px;height:44px;border-radius:50%;background:rgba(120,120,120,.55);display:flex;align-items:center;justify-content:center}

/* services */
.section-title{position:absolute;left:0;width:1200px;text-align:center;font-family:"Raleway",sans-serif;font-weight:700;font-size:27px}
.services-intro{left:0;top:712px;width:1200px;text-align:center;color:var(--white);font-size:13.5px;line-height:24px}
.service-card{position:absolute;top:912px;width:293px;height:234px;background:var(--white);border:1px solid var(--line);box-shadow:0 3px 4px rgba(0,0,0,.08);text-align:center}
.service-card h3{position:absolute;left:0;top:74px;width:100%;font-family:"Raleway",sans-serif;font-weight:600;font-size:15px;color:#222}
.service-card p{position:absolute;left:22px;top:98px;width:249px;font-size:12px;line-height:21px;color:var(--muted)}
.service-card .btn{left:101px;top:176px;width:90px;height:30px;font-size:11px}
.service-photo{position:absolute;top:782px;width:190px;height:190px;border-radius:50%;border:9px solid var(--white)}
.service-photo i{position:absolute;inset:0;border-radius:50%;border-bottom:4px solid var(--navy)}

/* diagnostic */
.diagnostic{position:absolute;left:0;top:1207px;width:1200px;height:411px;background:var(--panel);border-top:1px solid #e6e6e6;border-bottom:1px solid #e6e6e6}
.diag-title{left:131px;top:1275px;font-family:"Raleway",sans-serif;font-weight:700;font-size:28px;color:#222}
.diag-text{left:131px;width:445px;font-size:11.5px;line-height:21px;color:var(--muted)}
.video{position:absolute;left:614px;top:1278px;width:450px;height:263px;border:4px solid var(--white);box-shadow:0 1px 4px rgba(0,0,0,.2);background:linear-gradient(120deg,#d8cbbf,#b9a99a 45%,#8c8177 100%);overflow:hidden}
.video-bar{position:absolute;left:0;bottom:0;width:100%;height:26px;background:#1b1b1b}
.video-progress{position:absolute;left:0;bottom:26px;width:100%;height:4px;background:var(--navy)}
.play{position:absolute;left:199px;top:101px;width:44px;height:44px;border-radius:50%;background:rgba(255,255,255,.85);display:flex;align-items:center;justify-content:center}

/* testimonials */
.avatar{position:absolute;left:545px;top:1711px;width:110px;height:110px;border-radius:50%;border:4px solid var(--white);box-shadow:0 0 0 1px #ddd;background:linear-gradient(180deg,#e5e5e5,#cfc7bf)}
.avatar i{position:absolute;inset:0;border-radius:50%;border-bottom:4px solid var(--navy)}
.quote{left:210px;top:1846px;width:780px;text-align:center;font-style:italic;font-size:13px;line-height:24.5px;color:#555}
.quote-name{left:0;top:1932px;width:1200px;text-align:center;font-family:"Raleway",sans-serif;font-weight:700;font-size:13px;color:var(--navy)}
.quote-mark{font-family:"Open Sans",sans-serif;font-size:56px;color:var(--sky);line-height:1}

/* footer */
.site-footer{position:absolute;left:0;top:2000px;width:1200px;height:264px;background:var(--footer);color:var(--white)}
.footer-col{position:absolute;top:40px;font-size:11px;line-height:22px}
.footer-col h4{font-family:"Raleway",sans-serif;font-weight:700;font-size:13px;margin-bottom:14px;letter-spacing:.3px}
.footer-col p{margin-bottom:13px;line-height:20px}
.contact-row{display:flex;gap:10px;align-items:center}
.social{display:flex;align-items:center;gap:8px;margin-bottom:12px}
.social b{width:27px;height:27px;border-radius:50%;background:var(--white);display:block}
.footer-base{position:absolute;left:0;top:2264px;width:1200px;height:44px;background:var(--footer-base);color:#ddd;font-size:11px;display:flex;align-items:center;justify-content:center}
</style>
</head>
<body>

<header class="site-header">
  <div class="brand"><span class="brand-dot"></span>Restwell</div>
  <div class="phone">
    <span class="phone-icon"><svg width="14" height="14" viewBox="0 0 24 24"><path fill="#fff" d="M6.6 10.8a15.1 15.1 0 0 0 6.6 6.6l2.2-2.2c.3-.3.7-.4 1-.2 1.1.4 2.3.6 3.6.6.6 0 1 .4 1 1V20c0 .6-.4 1-1 1A17 17 0 0 1 3 4c0-.6.4-1 1-1h3.5c.6 0 1 .4 1 1 0 1.3.2 2.5.6 3.6.1.3 0 .7-.2 1z"/></svg></span>
    <span>PHONE : <strong>(+310) 555-0142</strong></span>
  </div>
  <div class="appt">MAKE AN APPOINTMENT</div>
  <nav class="main-nav">
    <span class="current" style="left:458px">HOME</span>
    <span style="left:544px">DIAGNOSIS</span>
    <span style="left:657px">TREATMENT OPTIONS</span>
    <span style="left:829px">ABOUT US</span>
    <span style="left:938px">CONTACT US</span>
    <svg style="position:absolute;left:1053px;top:0" width="15" height="15" viewBox="0 0 16 16"><circle cx="6.5" cy="6.5" r="5" fill="none" stroke="#c3cbd8" stroke-width="1.6"/><path d="M10.5 10.5 15 15" stroke="#c3cbd8" stroke-width="1.6"/></svg>
  </nav>
  <svg style="position:absolute;left:454px;top:60px" width="48" height="12" viewBox="0 0 48 12"><path d="M2 2 Q24 14 46 2" fill="none" stroke="#0b4a85" stroke-width="3"/></svg>
</header>
<div class="nav-mark" style="z-index:4"></div>

<section class="hero">
  <div class="hero-photo" role="img" aria-label="Photo of a doctor with a stethoscope reviewing a tablet with a female patient"></div>
  <svg class="hero-curve" viewBox="0 0 1200 425" preserveAspectRatio="none">
    <path d="M0 55 Q380 240 700 185 Q960 140 1200 40 L1200 425 L0 425 Z" fill="#a9b8dc"/>
    <path d="M0 78 Q330 215 640 192 Q950 165 1200 50 L1200 425 L0 425 Z" fill="#0b4a85"/>
  </svg>
  <div class="abs hero-kicker">DIAGNOSTIC &amp;</div>
  <h1 class="abs hero-title">TREATMENT SOLUTION</h1>
  <p class="abs hero-text">Lorem ipsum dolor sit amet, consectetur adipiscing elit, sed do eiusmod tempor incididunt...</p>
  <div class="btn" style="left:131px;top:391px;width:136px;height:40px">LEARN MORE INFO</div>
  <div class="slide-arrow" style="left:40px"><svg width="10" height="14" viewBox="0 0 10 14"><path d="M7 2 2 7l5 5" fill="none" stroke="#fff" stroke-width="2"/></svg></div>
  <div class="slide-arrow" style="left:1116px"><svg width="10" height="14" viewBox="0 0 10 14"><path d="M3 2l5 5-5 5" fill="none" stroke="#fff" stroke-width="2"/></svg></div>
</section>

<section class="services">
  <h2 class="section-title" style="top:675px;color:#fff">OUR SERVICES</h2>
  <p class="abs services-intro">Lorem ipsum dolor sit amet, consectetur adipiscing elit, sed do eiusmod tempor incididunt ut labore et dolore magna aliqua.<br>Ut enim ad minim veniam, quis nostrud exercitation ullamco laboris nisi ut aliquip...</p>

  <article class="service-card" style="left:132px">
    <h3>SNORING</h3>
    <p>Lorem ipsum dolor sit amet, consectetur adipis cing elit, sed do eiusmod tempor incididunt magna aliqua.enim ad minim...</p>
    <div class="btn">READ MORE</div>
  </article>
  <article class="service-card" style="left:454px">
    <h3>SLEEP DISORDERS</h3>
    <p>Lorem ipsum dolor sit amet, consectetur adipis cing elit, sed do eiusmod tempor incididunt magna aliqua.enim ad minim...</p>
    <div class="btn">READ MORE</div>
  </article>
  <article class="service-card" style="left:775px">
    <h3>RESPIRATORY PROBLEMS.</h3>
    <p>Lorem ipsum dolor sit amet, consectetur adipis cing elit, sed do eiusmod tempor incididunt magna aliqua.enim ad minim...</p>
    <div class="btn">READ MORE</div>
  </article>

  <div class="service-photo" style="left:183px;background:linear-gradient(160deg,#c9d3e3,#eef1f5 60%,#9aa9c0)" role="img" aria-label="Photo of a man snoring on a pillow"><i></i></div>
  <div class="service-photo" style="left:505px;background:linear-gradient(160deg,#5a5f73,#9ea6bd 55%,#d7dbe6)" role="img" aria-label="Photo of a woman lying awake in bed"><i></i></div>
  <div class="service-photo" style="left:826px;background:linear-gradient(160deg,#d6d6d6,#b99a86 50%,#e7eef0)" role="img" aria-label="Photo of a man wearing an oxygen mask"><i></i></div>
</section>

<section class="diagnostic"></section>
<h2 class="abs diag-title">DIAGNOSTIC TECHNIQUES</h2>
<p class="abs diag-text" style="top:1322px">Lorem ipsum dolor sit amet, consectetur adipiscing elit, sed do eiusmod tempor nostrud exercitation ullamco laboris nisi ut aliquip ex ea commodo consequat. Duis aute irure dolor in reprehenderit in voluptate velit esse...</p>
<p class="abs diag-text" style="top:1400px">Dorem ipsum dolor sit amet, consectetur adipiscing elit, sed do eiusmod tempor nostrud exercitation ullamco laboris nisi ut aliquip ex ea commodo consequat. Duis aute irure dolor in reprehenderit in voluptate velit esse...</p>
<div class="btn" style="left:131px;top:1492px;width:151px;height:40px;gap:6px">VIEW MORE VIDEOS <svg width="11" height="11" viewBox="0 0 12 12"><circle cx="6" cy="6" r="6" fill="#0b4a85"/><path d="M5 3.5 7.5 6 5 8.5" fill="none" stroke="#fff" stroke-width="1.5"/></svg></div>
<div class="video" role="img" aria-label="Video still of a patient lying on a couch while a clinician takes notes">
  <div class="play"><svg width="16" height="16" viewBox="0 0 16 16"><path d="M5 2.5l9 5.5-9 5.5z" fill="#0b4a85"/></svg></div>
  <div class="video-progress"></div>
  <div class="video-bar">
    <svg style="position:absolute;left:12px;top:8px" width="10" height="10" viewBox="0 0 10 10"><path d="M1 0l9 5-9 5z" fill="#ccc"/></svg>
    <span style="position:absolute;left:74px;top:5px;font-size:10px;color:#ddd">0:00 / 3:00</span>
  </div>
</div>

<section class="testimonials">
  <h2 class="section-title" style="top:1660px;color:#222">TESTIMONIALS</h2>
  <svg class="abs" style="left:468px;top:1746px" width="18" height="40" viewBox="0 0 18 40"><path d="M16 2 3 20l13 18" fill="none" stroke="#c8cdd8" stroke-width="1.5"/></svg>
  <svg class="abs" style="left:714px;top:1746px" width="18" height="40" viewBox="0 0 18 40"><path d="M2 2l13 18L2 38" fill="none" stroke="#c8cdd8" stroke-width="1.5"/></svg>
  <div class="avatar" role="img" aria-label="Portrait photo of the reviewer"><i></i></div>
  <span class="abs quote-mark" style="left:178px;top:1830px">&ldquo;</span>
  <p class="abs quote">Adipiscing elit, sed do eiusmod tempor incididunt ut labore et dolore magna aliqua. Ut enim ad minim veniam, quis nostrud exercitation ullamco laboris nisi ut aliquip ex ea commodo consequat. Duis aute irure dolor in reprehenderit in voluptate velit esse cillum dolore eu fugiat nulla pariatur...</p>
  <span class="abs quote-mark" style="left:762px;top:1898px">&rdquo;</span>
  <div class="abs quote-name">-JOHN DOE</div>
</section>

<footer class="site-footer">
  <div class="footer-col" style="left:131px;width:220px">
    <h4>SPECIALS</h4>
    <p>Aliquip ex ea commodo consequat. Duis aute irure dolorreprehenderit...</p>
    <p style="margin-top:20px">Aliquip ex ea commodo consequat. Duis aute irure dolorreprehenderit...</p>
    <p style="margin-top:20px">Aliquip ex ea commodo consequat. Duis aute irure dolorreprehenderit...</p>
  </div>
  <div class="footer-col" style="left:444px;width:230px">
    <h4>CONTACT INFO</h4>
    <div style="font-weight:700;font-size:10px">RESTWELL</div>
    <div class="contact-row"><svg width="9" height="12" viewBox="0 0 10 14"><path d="M5 0a5 5 0 0 1 5 5c0 4-5 9-5 9S0 9 0 5a5 5 0 0 1 5-5z" fill="#fff"/><circle cx="5" cy="5" r="2" fill="#2b2a30"/></svg>Restwell 8, 22 Harbour Lane</div>
    <div style="padding-left:19px">Northgate, Riverton-210</div>
    <div class="contact-row" style="margin-top:6px"><svg width="11" height="11" viewBox="0 0 24 24"><path fill="#fff" d="M6.6 10.8a15.1 15.1 0 0 0 6.6 6.6l2.2-2.2c.3-.3.7-.4 1-.2 1.1.4 2.3.6 3.6.6.6 0 1 .4 1 1V20c0 .6-.4 1-1 1A17 17 0 0 1 3 4c0-.6.4-1 1-1h3.5c.6 0 1 .4 1 1 0 1.3.2 2.5.6 3.6.1.3 0 .7-.2 1z"/></svg>Ph: 02 5550 1920</div>
    <div class="contact-row"><svg width="11" height="11" viewBox="0 0 12 12"><rect x="0" y="3" width="12" height="8" fill="#fff"/><rect x="3" y="0" width="6" height="4" fill="#fff"/></svg>Fax: 02 5550 1934</div>
    <div class="contact-row" style="margin-top:4px"><svg width="11" height="9" viewBox="0 0 12 9"><rect width="12" height="9" fill="#fff"/><path d="M0 0l6 5 6-5" fill="none" stroke="#2b2a30"/></svg>hello@restwell.example</div>
  </div>
  <div class="footer-col" style="left:711px;width:200px">
    <h4>OFFICE HOURS</h4>
    <div>Mon-Fri : 8.30am to 5.30pm</div>
    <div>Sat : 8.30 to 12. 30 pm</div>
    <div>Public Holidays : Holiday!</div>
    <div style="text-decoration:underline">By Special appointments</div>
  </div>
  <div class="footer-col" style="left:958px;width:150px">
    <h4>FOLLOW US</h4>
    <div class="social"><b></b>: Friendnet</div>
    <div class="social"><b></b>: Chirpline</div>
    <div class="social"><b></b>: Worklink</div>
    <div class="social"><b></b>: Circleplus</div>
  </div>
</footer>
<div class="footer-base">Copyright © 2017. Restwell. All rights reserved.</div>

</body>
</html>
```